Stationary - Based On Previous Design

Basic stationary with a header and footer

Target Market(s)

Friends, Colleagues, More friendly than professional

Industry/Entity Type

legal/personal

Colors
00AB8E
00BBA5
67D7C9
C6EFE9
E9F9F6

Requirements
Must have
• Green & White
Nice to have
• I like the "G" on the business card and was thinking that would be for both G's in "PellaNote"
Should not have
• other colors

```html
<!DOCTYPE html>
<html lang="en">
<head>
<meta charset="utf-8">
<title>PellaNote Stationery</title>
<link rel="stylesheet" href="https://fonts.googleapis.com/css2?family=Nunito:wght@500;600;700;800&family=Roboto:wght@300;400;500&display=swap">
<style>
  :root {
    --backdrop: #4b4b50;
    --paper: #ffffff;
    --green: #1d5a2d;
    --ink: #2b2b2b;
    --ink-soft: #454545;
    --accent: #e23b2b;
    --rule-grey: #9a9a9a;
    --ghost: #f3f3f3;
  }
  * { margin: 0; padding: 0; box-sizing: border-box; }
  html, body { width: 1194px; height: 1200px; overflow: hidden; }
  body { background: var(--backdrop); position: relative; font-family: "Roboto", sans-serif; color: var(--ink); }

  .letterhead { position: absolute; left: 61px; top: 177px; width: 596px; height: 843px; background: var(--paper); overflow: hidden; }
  .ghost-mark { position: absolute; border-radius: 50%; background: var(--ghost); }
  .letterhead .ghost-mark { width: 230px; height: 230px; right: -70px; top: -40px; }

  .brand { position: absolute; display: flex; align-items: center; gap: 8px; font-family: "Nunito", sans-serif; font-weight: 800; white-space: nowrap; }
  .brand-dot { border-radius: 50%; background: var(--green); flex: none; }
  .letterhead .brand { left: 38px; top: 44px; font-size: 30px; color: var(--ink-soft); }
  .letterhead .brand-dot { width: 40px; height: 40px; }

  .sender { position: absolute; left: 43px; top: 172px; }
  .sender-name { font-size: 12.5px; font-weight: 500; }
  .sender-name .surname { color: var(--accent); }
  .sender-role { font-size: 10px; font-weight: 300; margin-top: 4px; }
  .sender-lines { list-style: none; margin-top: 10px; font-size: 11.5px; font-weight: 300; line-height: 18.5px; }
  .sender-lines b { font-weight: 500; }
  .sender-lines .red { color: var(--accent); }
  .letter-date { position: absolute; right: 41px; top: 247px; font-size: 11.5px; font-weight: 300; }

  .letter-body { position: absolute; left: 43px; top: 314px; width: 511px; font-size: 11.3px; font-weight: 300; line-height: 19.8px; text-align: justify; color: var(--ink-soft); }
  .letter-body p + p { margin-top: 19.5px; }

  .signoff { position: absolute; left: 43px; top: 692px; }
  .signature { width: 100px; height: 26px; background: linear-gradient(90deg, #ececec, #f7f7f7); border-radius: 3px; }
  .signoff-name { font-size: 12.5px; font-weight: 500; margin-top: 8px; }
  .signoff-role { font-size: 11px; font-weight: 300; margin-top: 3px; }

  .letter-footer { position: absolute; left: 0; bottom: 0; width: 100%; height: 52px; border-top: 4px solid var(--rule-grey); background: var(--green); display: flex; align-items: center; gap: 18px; padding: 0 40px; font-family: "Nunito", sans-serif; font-size: 10px; font-weight: 600; color: #fff; white-space: nowrap; }
  .footer-item { display: flex; align-items: center; gap: 6px; }
  .footer-item .mini-dot { width: 12px; height: 12px; border-radius: 50%; background: #fff; }
  .icon-chip { width: 15px; height: 15px; border-radius: 50%; background: #fff; display: flex; align-items: center; justify-content: center; }

  .card { position: absolute; left: 735px; width: 401px; height: 229px; overflow: hidden; }
  .card-front { top: 522px; background: var(--green); }
  .card-front .brand { left: 50%; top: 50%; transform: translate(-50%, -50%); font-size: 34px; color: #fff; gap: 10px; }
  .card-front .brand-dot { width: 44px; height: 44px; background: #fff; }

  .card-back { top: 791px; background: var(--paper); }
  .card-back .ghost-mark { width: 150px; height: 150px; right: -45px; top: 5px; }
  .card-back .brand { left: 29px; top: 26px; font-size: 22px; color: var(--ink-soft); gap: 6px; }
  .card-back .brand-dot { width: 28px; height: 28px; }
  .card-name { position: absolute; left: 31px; top: 99px; font-family: "Nunito", sans-serif; font-size: 19px; font-weight: 700; color: var(--ink-soft); }
  .card-role { position: absolute; left: 31px; top: 124px; font-family: "Nunito", sans-serif; font-size: 12px; font-weight: 600; color: var(--green); }
  .card-rule { position: absolute; left: 31px; top: 150px; width: 48px; height: 1px; background: #aaa; }
  .card-contacts { position: absolute; left: 31px; top: 160px; list-style: none; font-family: "Nunito", sans-serif; font-size: 12.5px; font-weight: 600; color: var(--ink-soft); line-height: 19.5px; }
  .card-contacts li { display: flex; align-items: center; gap: 6px; }
  .card-contacts .icon-chip { width: 12px; height: 12px; background: var(--green); }
  .card-band { position: absolute; left: 0; bottom: 0; width: 100%; height: 19px; border-top: 4px solid var(--rule-grey); background: var(--green); }
</style>
</head>
<body>

<section class="letterhead">
  <div class="ghost-mark"></div>
  <div class="brand"><span class="brand-dot"></span>PellaNote</div>

  <div class="sender">
    <p class="sender-name">Mara <span class="surname">Ellis</span></p>
    <p class="sender-role">Designer</p>
    <ul class="sender-lines">
      <li><b class="red">A</b> <b>:</b> New York City- Zip Code - 000</li>
      <li><b>W</b> <b>:</b> www.yourwebsitename.com</li>
      <li><b class="red">P</b> <b>:</b> +000 123 456 789</li>
    </ul>
  </div>
  <p class="letter-date">Date : 25 September, 2030</p>

  <div class="letter-body">
    <p>Lorem ipsum dolor sit amet, consectetur adipisicing elit, sed do eiusmod tempor incididunt ut labore et dolore magna aliqua. Ut enim ad minim veniam, quis nostrud exercitation ullamco laboris nisi ut aliquip ex ea commodo consequat.</p>
    <p>Excepteur sint occaecat cupidatat non proident, sunt in culpa qui officia deserunt mollit anim id est laborum. Sed ut perspiciatis unde omnis iste natus error sit voluptatem accusantium doloremque laudantium, totam rem aperiam, eaque ipsa quae ab illo inventore veritatis et quasi architecto beatae vitae dicta sunt explicabo. Nemo enim ipsam voluptatem quia voluptas sit aspernatur aut odit aut quia consequuntur voluptatem sequi nesciunt.</p>
    <p>Voluptatem accusantium doloremque laudantium, totam rem aperiam, eaque ipsa quae ab illo inventore veritatis et quasi architecto beatae vitae dicta sunt explicabo. Nemo enim ipsam voluptatem quia voluptas sit aspernatur aut odit aut quia consequuntur voluptatem sequi nesciunt.</p>
    <p>Neque porro quisquam dolorem ipsum quia dolor sit amet, consecteturtempora incidunt labore dolore magnam aliquam quaerat voluptatem.</p>
  </div>

  <div class="signoff">
    <div class="signature" role="img" aria-label="Handwritten signature of Jonah Reed"></div>
    <p class="signoff-name">Jonah Reed</p>
    <p class="signoff-role">Manager</p>
  </div>

  <footer class="letter-footer">
    <span class="footer-item"><span class="mini-dot"></span>Daniel Ortvale</span>
    <span class="footer-item">
      <span class="icon-chip"><svg width="9" height="7" viewBox="0 0 9 7"><rect x="0.5" y="0.5" width="8" height="6" fill="none" stroke="#1d5a2d"/><path d="M0.5 0.5 L4.5 4 L8.5 0.5" fill="none" stroke="#1d5a2d"/></svg></span>dortvale@ortvalefirm.com
    </span>
    <span class="footer-item">
      <span class="icon-chip"><svg width="8" height="10" viewBox="0 0 8 10"><path d="M4 9.5 C1 6 0.5 4.8 0.5 3.8 A3.5 3.5 0 0 1 7.5 3.8 C7.5 4.8 7 6 4 9.5Z" fill="#1d5a2d"/><circle cx="4" cy="3.8" r="1.3" fill="#fff"/></svg></span>418 N Larkmoor Ave Brookhaven, IL 60455
    </span>
  </footer>
</section>

<section class="card card-front">
  <div class="brand"><span class="brand-dot"></span>PellaNote</div>
</section>

<section class="card card-back">
  <div class="ghost-mark"></div>
  <div class="brand"><span class="brand-dot"></span>PellaNote</div>
  <p class="card-name">Daniel Ortvale</p>
  <p class="card-role">President</p>
  <div class="card-rule"></div>
  <ul class="card-contacts">
    <li><span class="icon-chip"><svg width="7" height="5" viewBox="0 0 7 5"><rect x="0.4" y="0.4" width="6.2" height="4.2" fill="none" stroke="#fff" stroke-width="0.8"/><path d="M0.4 0.4 L3.5 3 L6.6 0.4" fill="none" stroke="#fff" stroke-width="0.8"/></svg></span>dortvale@ortvalefirm.com</li>
    <li><span class="icon-chip"><svg width="6" height="8" viewBox="0 0 8 10"><path d="M4 9.5 C1 6 0.5 4.8 0.5 3.8 A3.5 3.5 0 0 1 7.5 3.8 C7.5 4.8 7 6 4 9.5Z" fill="#fff"/></svg></span>418 N Larkmoor Ave Brookhaven, IL 60455</li>
  </ul>
  <div class="card-band"></div>
</section>

</body>
</html>
```